Book Cover Design RTM

Want a new book cover but want to use the same photo and change the sub name. This is for a brand called "Amber Meadow Living". The book is called "Quiet Steps, Bright Days"

This is for a 8.5 * 11 book size

We really want to brand the Amber Meadow Living

I've attached a sample of an old book cover, the photo I want used and the amber meadow living logo

Requirements
Must have
• Must have the logo,

must have the book title. "Quiet Steps, Bright Days"

Must have "Featuring" The Amber Meadow Living Tumble Card Game"

On the back put the logo and Amber Meadow Living Nutrition

must have the authors name "Norma Plaskett" on the page

"The Golden Stride Map"
Nice to have
• Amber Meadow Living Presents:

the book title

```html
<!DOCTYPE html>
<html lang="en">
<head>
<meta charset="utf-8">
<title>Quiet Steps, Bright Days — Book Cover</title>
<link rel="stylesheet" href="https://fonts.googleapis.com/css2?family=Anton&family=Oswald:wght@400;600&family=Montserrat:wght@300;400;600&family=Questrial&display=swap">
<style>
  :root {
    --backdrop: #d9d9d9;
    --cover: #000000;
    --ink: #ffffff;
    --ink-dark: #000000;
    --accent: #6fd3b8;
    --spine-edge: #1c1c1c;
    --photo-top: #1e1714;
    --photo-mid: #0c0c0c;
    --photo-low: #111111;
  }
  * { margin: 0; padding: 0; box-sizing: border-box; }
  html, body { width: 1200px; height: 780px; overflow: hidden; background: var(--backdrop); }
  .canvas { position: relative; width: 1200px; height: 780px; }

  .cover-spread {
    position: absolute; left: 60px; top: 60px; width: 1080px; height: 660px;
    background: var(--cover); color: var(--ink);
  }

  /* Back cover */
  .back-cover { position: absolute; left: 0; top: 0; width: 510px; height: 660px; }
  .brand-mark {
    position: absolute; left: 180px; top: 66px; width: 150px; height: 150px;
    border: 3px solid var(--ink); border-radius: 50%;
  }
  .back-brand {
    position: absolute; left: 0; width: 510px; top: 252px; text-align: center;
    font-family: "Questrial", sans-serif; font-size: 24px; letter-spacing: 3px; text-transform: uppercase;
  }
  .back-brand-line {
    position: absolute; left: 0; width: 510px; top: 290px; text-align: center;
    font-family: "Questrial", sans-serif; font-size: 9px; letter-spacing: 2.5px; text-transform: uppercase;
  }
  .back-blurb {
    position: absolute; left: 58px; top: 340px; width: 394px;
    font-family: "Oswald", sans-serif; font-size: 13px; line-height: 20px;
    text-transform: uppercase; text-align: justify; text-align-last: left;
  }
  .back-note {
    position: absolute; left: 58px; top: 544px; width: 250px;
    font-family: "Oswald", sans-serif; font-size: 13px; line-height: 20px; text-transform: uppercase;
  }
  .barcode-box {
    position: absolute; left: 334px; top: 538px; width: 118px; height: 62px;
    background: var(--ink); color: var(--ink-dark);
    display: flex; align-items: center; justify-content: center;
    font-family: "Oswald", sans-serif; font-size: 13px; text-transform: uppercase;
  }

  /* Spine */
  .spine {
    position: absolute; left: 510px; top: 0; width: 60px; height: 660px;
    border-left: 1px solid var(--spine-edge); border-right: 1px solid var(--spine-edge);
  }
  .spine-text {
    position: absolute; left: 0; width: 60px; writing-mode: vertical-rl;
    display: flex; align-items: center; justify-content: flex-start;
  }
  .spine-brand { top: 36px; font-family: "Questrial", sans-serif; font-size: 9px; letter-spacing: 1.5px; text-transform: uppercase; }
  .spine-mark {
    position: absolute; left: 19px; top: 152px; width: 22px; height: 22px;
    border: 2px solid var(--ink); border-radius: 50%;
  }
  .spine-title { top: 212px; font-family: "Oswald", sans-serif; font-weight: 600; font-size: 24px; text-transform: uppercase; letter-spacing: 0.5px; }
  .spine-author { top: 506px; font-family: "Montserrat", sans-serif; font-weight: 400; font-size: 13px; text-transform: uppercase; }

  /* Front cover */
  .front-cover { position: absolute; left: 570px; top: 0; width: 510px; height: 660px; overflow: hidden; }
  .author-photo {
    position: absolute; left: 226px; top: 0; width: 284px; height: 660px;
    background: linear-gradient(180deg, var(--photo-top) 0%, var(--photo-mid) 45%, var(--photo-low) 100%);
  }
  .vertical-stack { position: absolute; writing-mode: vertical-rl; transform: rotate(180deg); }
  .front-brand {
    left: 34px; top: 44px; height: 290px; width: 44px;
    font-family: "Questrial", sans-serif; text-transform: uppercase;
  }
  .front-brand .name { font-size: 20px; letter-spacing: 1.5px; line-height: 26px; }
  .front-brand .sub { font-size: 9px; letter-spacing: 3px; line-height: 16px; }
  .front-mark {
    position: absolute; left: 36px; top: 346px; width: 38px; height: 38px;
    border: 3px solid var(--ink); border-radius: 50%;
  }
  .front-title {
    left: 86px; top: 44px; height: 360px; width: 128px;
    font-family: "Anton", sans-serif; font-weight: 400; font-size: 62px; line-height: 64px; text-transform: uppercase;
  }
  .rule { position: absolute; left: 34px; width: 174px; height: 2px; background: var(--ink); }
  .rule-top { top: 426px; }
  .rule-mid { top: 484px; }
  .rule-bottom { top: 558px; }
  .stride-map { position: absolute; left: 34px; top: 432px; width: 174px; font-family: "Montserrat", sans-serif; line-height: 22px; }
  .stride-map .lead { font-weight: 600; font-size: 14px; letter-spacing: 1.2px; }
  .stride-map .accent { color: var(--accent); font-weight: 400; font-size: 19px; letter-spacing: 4px; text-transform: uppercase; }
  .game-line { position: absolute; left: 34px; top: 490px; width: 174px; font-family: "Montserrat", sans-serif; line-height: 21px; }
  .game-line .lead { font-weight: 600; font-size: 13px; letter-spacing: 1px; }
  .game-line .accent { color: var(--accent); font-weight: 400; font-size: 17px; text-transform: uppercase; }
  .front-author {
    position: absolute; left: 34px; top: 588px;
    font-family: "Montserrat", sans-serif; font-weight: 300; font-size: 24px; text-transform: uppercase; letter-spacing: 0.5px;
  }
</style>
</head>
<body>
<main class="canvas">
  <section class="cover-spread">

    <div class="back-cover">
      <div class="brand-mark"></div>
      <div class="back-brand">Amber Meadow Living</div>
      <div class="back-brand-line">Amber Meadow Living Nutrition</div>
      <p class="back-blurb">Lorem ipsum dolor sit amet, consectetuer adipiscing elit, sed diam nonummy nibh euismod tincidunt ut laoreet dolore magna aliquam erat volutpat. Ut wisi enim ad minim veniam, quis nostrud exerci tation ullamcorper suscipit lobortis nisl ut aliquip ex ea commodo consequat. Duis autem vel eum iriure dolor in hendrerit in vulputate velit esse molestie consequat, vel illum dolore eu feugiat nulla facilisis at vero eros et accumsan et iusto odio dignissim qui blandit praesent luptatum zzril delenit augue duis dolore te feugait nulla facilisi.</p>
      <p class="back-note">Lorem ipsum dolor sit amet, consectetuer adipiscing elit, sed diam nonummy nibh euismod tincidunt ut laoreet dolore magna</p>
      <div class="barcode-box">Bar Code</div>
    </div>

    <div class="spine">
      <div class="spine-text spine-brand">Amber Meadow Living</div>
      <div class="spine-mark"></div>
      <div class="spine-text spine-title">Quiet Steps Bright Days</div>
      <div class="spine-text spine-author">Norma Plaskett</div>
    </div>

    <div class="front-cover">
      <div class="author-photo" role="img" aria-label="Photo of the author in workout clothes leaning on an exercise ball"></div>
      <div class="vertical-stack front-brand"><span class="name">Amber Meadow Living</span><span class="sub">Nutrition</span></div>
      <div class="front-mark"></div>
      <h1 class="vertical-stack front-title">Quiet Steps<br>Bright Days</h1>
      <div class="rule rule-top"></div>
      <div class="stride-map"><div class="lead">The Golden Stride</div><div class="accent">Map</div></div>
      <div class="rule rule-mid"></div>
      <div class="game-line"><div class="lead">The Amber Meadow</div><div class="accent">Living Tumble</div><div class="lead">Card Game</div></div>
      <div class="rule rule-bottom"></div>
      <div class="front-author">Norma Plaskett</div>
    </div>

  </section>
</main>
</body>
</html>
```